HARBORLINE AUTO GLASS

Mobile Glass Shop:

1) Windshield REPAIR 2)Windshield replacment 3) Rear Windshield Replacment 4) Side Window Replacment 5) car window replacment 6) Power Window Repair.

Schedual a service within 24 hour with one of our certified technicians.
Updates

See "brightvane auto repair" web site for referance on the nature of our buisness and service. www.brightvane-example.com

Coding

```html
<!DOCTYPE html>
<html lang="en">
<head>
<meta charset="utf-8">
<title>Harborline Auto Glass – Windshield Repair</title>
<link href="https://fonts.googleapis.com/css2?family=Oswald:wght@500;700&family=Lato:wght@400;700&display=swap" rel="stylesheet">
<style>
:root{
  --navy:#0b5e98;
  --blue:#1a7fc8;
  --sky:#139ee0;
  --pale:#e1f0f6;
  --ink:#222;
  --grey:#6b6b6b;
  --line:#d6d6d6;
  --white:#fff;
}
*{margin:0;padding:0;box-sizing:border-box}
html,body{width:1200px;height:3947px;overflow:hidden}
body{position:relative;font-family:'Lato',sans-serif;color:var(--ink);background:var(--white)}
a{text-decoration:none;color:inherit}
.abs{position:absolute}
.btn{position:absolute;display:flex;align-items:center;justify-content:center;background:var(--sky);color:var(--white);font-weight:700;clip-path:polygon(6% 0,100% 0,94% 100%,0 100%)}

.topbar{left:0;top:0;width:1200px;height:44px;background:var(--navy);display:flex;align-items:center;justify-content:center;gap:20px;color:var(--white);font-size:14px;font-weight:700}
.topbar .call{position:static;width:86px;height:28px;background:var(--white);color:var(--navy);font-size:14px}

.header{left:0;top:44px;width:1200px;height:97px}
.logo{left:143px;top:8px;display:flex;align-items:center;gap:10px}
.logo .mark{width:64px;height:80px;background:var(--blue)}
.logo .name{font-family:'Oswald',sans-serif;font-weight:500;color:var(--blue);font-size:22px;line-height:1.05;letter-spacing:1px;width:150px}
.nav{left:472px;top:46px;display:flex;gap:0;font-size:15px;font-weight:400;color:#333}
.nav a{position:absolute;white-space:nowrap}
.nav a.active{border-bottom:3px solid var(--sky);padding-bottom:4px}
.header .quote{left:926px;top:39px;width:127px;height:35px;font-size:15px}

.hero{left:0;top:141px;width:1200px;height:653px}
.hero h1{left:143px;top:184px;font-family:'Oswald',sans-serif;font-weight:700;font-size:80px;line-height:84px;color:var(--white)}
.hero .sub{left:143px;top:380px;font-size:33px;font-weight:700;color:var(--white)}
.hero .quote{left:143px;top:454px;width:180px;height:51px;font-size:18px}

.section-title{left:0;width:1200px;text-align:center;font-family:'Oswald',sans-serif;font-weight:700;color:var(--navy);font-size:64px;line-height:1}

.card{position:absolute;width:289px;height:336px;border:3px solid var(--line);background:var(--white);text-align:center;padding-top:30px}
.card.featured{border-top:10px solid var(--blue);padding-top:23px}
.card svg{width:84px;height:70px;stroke:var(--blue);fill:none;stroke-width:3;stroke-linecap:round;stroke-linejoin:round}
.card h3{font-size:18px;font-weight:700;margin-top:14px;color:#222}
.card p{font-size:14.5px;line-height:22.5px;color:var(--grey);margin:18px auto 0;width:230px}
.card .more{position:relative;margin:16px auto 0;width:134px;height:38px;font-size:13px}

.blog-bg{left:0;top:1763px;width:1200px;height:873px}
.post{position:absolute;width:443px;height:441px;background:var(--white);box-shadow:0 0 0 2px #e8e8e8}
.post .photo{width:100%;height:240px}
.post h3{margin:26px 0 0 27px;font-size:24px;font-weight:700;color:#222}
.post p{margin:18px 27px 0;font-size:14.5px;line-height:22.5px;color:var(--grey)}
.post .more{left:27px;bottom:0;width:158px;height:38px;font-size:13px}

.video{left:0;top:2532px;width:1200px;height:662px}
.play{left:550px;top:2908px;width:100px;height:100px;border-radius:50%;border:4px solid var(--white);background:var(--sky);display:flex;align-items:center;justify-content:center}

.cta{left:0;top:3194px;width:1200px;height:343px;background:var(--navy)}
.cta h2{position:absolute;top:76px;width:1200px;text-align:center;font-family:'Oswald',sans-serif;font-weight:700;font-size:66px;line-height:76px;color:var(--white)}
.cta .quote{left:510px;top:230px;width:178px;height:51px;font-size:19px}

.footer-col{top:3590px}
.footer-col h4{font-size:25px;font-weight:700;color:#222;margin-bottom:22px}
.footer-col li{list-style:none;font-size:13.5px;color:#555;line-height:28px}
.social{display:flex;gap:18px}
.social span{width:32px;height:32px;border-radius:50%;background:var(--navy)}
.chat{left:1118px;top:3778px;width:44px;height:44px;border-radius:50%;background:var(--navy);display:flex;align-items:center;justify-content:center}
.rule{left:0;top:3853px;width:1200px;height:1px;background:#dcdcdc}
.copy{left:0;top:3892px;width:1200px;text-align:center;font-size:13px;color:#555}
</style>
</head>
<body>

<div class="abs topbar">
  <span>Schedule a service within 24 hour with one of our certified technicians</span>
  <a class="btn call" href="#">CALL US</a>
</div>

<header class="abs header">
  <div class="abs logo">
    <span class="mark"></span>
    <span class="name">HARBORLINE AUTO GLASS</span>
  </div>
  <nav class="abs nav">
    <a class="active" style="left:0">HOME</a>
    <a style="left:81px">ABOUT</a>
    <a style="left:167px">SERVICES</a>
    <a style="left:270px">NEWS</a>
    <a style="left:346px">CONTACT</a>
  </nav>
  <a class="btn quote" href="#">GET A QUOTE</a>
</header>

<section class="abs hero">
  <svg class="abs" width="1200" height="653" viewBox="0 0 1200 653" style="left:0;top:0">
    <polygon points="0,0 1200,0 1200,653 0,653" fill="#1979c3"/>
    <polygon points="0,0 1200,0 1200,15 600,30 0,20" fill="#e9eef2"/>
    <polygon points="620,30 1200,15 1200,70 580,90" fill="#2aa0e0"/>
    <polygon points="560,560 1200,520 1200,653 480,653" fill="#2aa0e0"/>
    <polygon points="480,653 1200,600 1200,653" fill="#fff"/>
    <polygon points="490,75 1200,50 1200,560 590,605" fill="#6e8796" role="img" aria-label="Technician in blue gloves fitting a new windshield into a car"/>
    <circle cx="1117" cy="294" r="4" fill="#fff"/>
    <circle cx="1117" cy="326" r="4" fill="#2aa0e0"/>
    <circle cx="1117" cy="359" r="4" fill="#fff"/>
  </svg>
  <h1 class="abs">WINDSHIELD<br>REPAIR</h1>
  <p class="abs sub">Schedule online today</p>
  <a class="btn quote" href="#">GET A QUOTE</a>
</section>

<h2 class="abs section-title" style="top:862px">WHAT WE PROVIDE</h2>

<div class="card" style="left:144px;top:999px">
  <svg viewBox="0 0 84 70"><path d="M8 20 Q42 10 76 20 L82 52 Q42 46 2 52 Z"/><path d="M14 24 Q42 17 70 24 L74 46 Q42 42 10 46Z"/><path d="M38 28 l6 8 -4 6 M44 36 l6 -4"/></svg>
  <h3>Windshield Repair</h3>
  <p>Lorem ipsum dolor sitonsectetur adipiscing elit, sed do eiusmod tempor incididunt ut labore et dolore magna aliqua.</p>
  <a class="btn more" href="#">READ MORE</a>
</div>
<div class="card featured" style="left:455px;top:999px">
  <svg viewBox="0 0 84 70"><path d="M38 10 v8 M46 10 v8 M34 10 h16"/><path d="M6 24 h72 l-4 22 h-64 Z"/><path d="M12 30 h60 l-3 10 h-54Z"/><path d="M30 38 l4 -5 M40 38 l6 -6 M50 38 l4 -4"/><path d="M20 50 h44"/></svg>
  <h3>Windshield Replacment</h3>
  <p>Lorem ipsum dolor sitonsectetur adipiscing elit, sed do eiusmod tempor incididunt ut labore et dolore magna aliqua.</p>
  <a class="btn more" href="#">READ MORE</a>
</div>
<div class="card" style="left:766px;top:999px">
  <svg viewBox="0 0 84 70"><rect x="30" y="6" width="24" height="8" rx="3"/><path d="M14 24 Q42 12 70 24 L78 58 H6 Z"/><path d="M20 30 Q42 20 64 30 L70 52 H14Z"/><path d="M42 28 v22 M36 44 l6 -8 6 8"/></svg>
  <h3>Rear Windshield Replacment</h3>
  <p>Lorem ipsum dolor sitonsectetur adipiscing elit, sed do eiusmod tempor incididunt ut labore et dolore magna aliqua.</p>
  <a class="btn more" href="#">READ MORE</a>
</div>
<div class="card" style="left:144px;top:1359px">
  <svg viewBox="0 0 84 70"><path d="M18 32 L30 8 H64 a4 4 0 0 1 4 4 V62 a4 4 0 0 1 -4 4 H22 a4 4 0 0 1 -4 -4 Z"/><path d="M18 40 H68"/><path d="M30 8 L44 34"/><circle cx="46" cy="38" r="3"/><path d="M62 48 h4"/></svg>
  <h3>Side Window Replacment</h3>
  <p>Lorem ipsum dolor sitonsectetur adipiscing elit, sed do eiusmod tempor incididunt ut labore et dolore magna aliqua.</p>
  <a class="btn more" href="#">READ MORE</a>
</div>
<div class="card" style="left:455px;top:1359px">
  <svg viewBox="0 0 84 70"><path d="M24 6 H54 L70 24 V54 a4 4 0 0 1 -4 4 H34 L24 66 Z"/><path d="M30 12 H52 L62 24 H30 Z"/><path d="M32 34 h8"/><path d="M24 40 v12"/></svg>
  <h3>Car Window Replacment</h3>
  <p>Lorem ipsum dolor sitonsectetur adipiscing elit, sed do eiusmod tempor incididunt ut labore et dolore magna aliqua.</p>
  <a class="btn more" href="#">READ MORE</a>
</div>
<div class="card" style="left:766px;top:1359px">
  <svg viewBox="0 0 84 70"><path d="M8 24 H18 L36 10 V60 L18 46 H8 Z"/><path d="M18 24 V46"/><path d="M66 8 L52 34 H68 L54 62"/></svg>
  <h3>Power Window Repair</h3>
  <p>Lorem ipsum dolor sitonsectetur adipiscing elit, sed do eiusmod tempor incididunt ut labore et dolore magna aliqua.</p>
  <a class="btn more" href="#">READ MORE</a>
</div>

<svg class="abs blog-bg" width="1200" height="873" viewBox="0 0 1200 873">
  <polygon points="0,0 1200,77 1200,873 0,873" fill="var(--pale)"/>
</svg>

<h2 class="abs section-title" style="top:1918px">FROM THE BLOG</h2>

<article class="post" style="left:146px;top:2040px">
  <div class="photo" role="img" aria-label="Technician lifting a windshield pane with suction cups" style="background:linear-gradient(135deg,#3b4a58,#9aa7b0)"></div>
  <h3>Sed ut perspiciatis unde omnis iste</h3>
  <p>Lorem ipsum dolor sit amet, consectetur adipiscing elit, sed do eiusmod tempor incididunt ut labore et dolore magna aliqua. Quis ipsum suspendisse ultrices gravida.</p>
  <a class="btn more" href="#">READ MORE</a>
</article>
<article class="post" style="left:611px;top:2040px">
  <div class="photo" role="img" aria-label="Close-up of a cracked car side mirror" style="background:linear-gradient(135deg,#1f2a33,#7e8c96)"></div>
  <h3>Excepteur sint occaecat cupidata</h3>
  <p>Lorem ipsum dolor sit amet, consectetur adipiscing elit, sed do eiusmod tempor incididunt ut labore et dolore magna aliqua. Quis ipsum suspendisse ultrices gravida.</p>
  <a class="btn more" href="#">READ MORE</a>
</article>

<svg class="abs video" width="1200" height="662" viewBox="0 0 1200 662">
  <polygon points="0,108 1200,0 1200,662 0,662" fill="#5e6f78" role="img" aria-label="Two technicians setting a windshield onto a car with suction cups"/>
</svg>
<div class="abs play"><svg width="36" height="40" viewBox="0 0 36 40"><polygon points="6,2 34,20 6,38" fill="#fff"/></svg></div>

<section class="abs cta">
  <h2>DON'T WAIT, SCHEDULE<br>YOUR APPOINTMENT TODAY!</h2>
  <a class="btn quote" href="#">GET A QUOTE</a>
</section>

<div class="abs footer-col" style="left:146px">
  <h4>Services</h4>
  <ul><li>Windshield REPAIR</li><li>Windshield replacment</li><li>Rear Windshield Replacment</li><li>Side Window Replacment</li><li>Car window replacment</li><li>Power Window Repair</li></ul>
</div>
<div class="abs footer-col" style="left:419px">
  <h4>Quick Links</h4>
  <ul><li>Home</li><li>About Us</li><li>Services</li><li>News</li><li>Contact Us</li></ul>
</div>
<div class="abs footer-col" style="left:648px">
  <h4>Other Links</h4>
  <ul><li>Terms of Use</li><li>Privacy Policy</li><li>Products</li><li>Resource Center</li></ul>
</div>
<div class="abs footer-col" style="left:876px">
  <h4>Social Media</h4>
  <div class="social"><span aria-label="Social profile"></span><span aria-label="Social profile"></span><span aria-label="Social profile"></span><span aria-label="Social profile"></span></div>
</div>

<div class="abs chat"><svg width="24" height="22" viewBox="0 0 24 22"><path d="M2 2 H22 V15 H9 L4 20 V15 H2 Z" fill="#fff"/></svg></div>
<div class="abs rule"></div>
<p class="abs copy">© 2022 Harborline Auto Glass.All Rights Reserved &nbsp;| &nbsp;Privacy &nbsp;| &nbsp;Terms of use &nbsp;| &nbsp;Sitemap</p>

</body>
</html>
```